Automotive component supplier needs a business card design

We need a business card design for our company called Velran Global Components Ltd based in the UK. We are a supplier of interior and exterior components to premium car manufacturers such as Corvel Ashby, Hadley Fenn, Marquist and Tavarelli. We would like to see a modern business card design that uses the colour blue.

Target Market(s)

Premium automotive car manufacturers.

Industry/Entity Type

Automotive

Contact Information for Business Card

Company Name : Velran Global Components Limited
Address: 17 Marlow Yard, Upper Heath, Warwick, CV31 8QL, United Kingdom
Web Address : www.velrancomponents-example.co.uk

Font styles to use
Other font styles liked:
• Helvetica

Colors
3176b5
0255a3
85acd3
cfdeed
cee9f5
85cae6
34a6d7
0692cd
9bcb3c

Requirements
Must have
• Clear company logo and a mixture of blue colours.
Nice to have
• A high quality modern image.
Should not have
• Multiple colours.

```html
<!DOCTYPE html>
<html lang="en">
<head>
<meta charset="utf-8">
<title>Velran Global Components – Business Card</title>
<link href="https://fonts.googleapis.com/css2?family=Lato:wght@400;700;900&display=swap" rel="stylesheet">
<style>
  :root {
    --blue-brand: #0692cd;
    --blue-deep: #0255a3;
    --green-accent: #9bcb3c;
    --paper: #ffffff;
    --ink: #2b2b2b;
    --rule: #8a8a8a;
    --backdrop: #3b3d3f;
  }
  * { margin: 0; padding: 0; box-sizing: border-box; }
  html, body { width: 1200px; height: 800px; overflow: hidden; }
  body {
    background: var(--backdrop);
    font-family: "Lato", Helvetica, Arial, sans-serif;
    position: relative;
  }
  .card {
    position: absolute;
    width: 540px;
    height: 308px;
    border-radius: 3px;
    overflow: hidden;
  }
  .brand-name {
    font-weight: 900;
    letter-spacing: 0.3px;
    line-height: 1.05;
    white-space: nowrap;
  }
  /* Front */
  .card-front {
    left: 70px; top: 90px;
    background: var(--blue-brand);
    color: var(--paper);
  }
  .card-front .brand-name {
    position: absolute;
    left: 0; right: 0; top: 104px;
    text-align: center;
    font-size: 38px;
    color: var(--paper);
  }
  .front-web {
    position: absolute;
    left: 0; right: 0; bottom: 44px;
    text-align: center;
    font-size: 13px;
    letter-spacing: 1.6px;
  }
  .front-web .tld { color: var(--green-accent); }
  /* Back */
  .card-back {
    left: 590px; top: 402px;
    background: var(--paper);
    color: var(--ink);
    border-bottom: 8px solid var(--blue-brand);
  }
  .card-back .brand-name {
    position: absolute;
    left: 38px; top: 44px;
    font-size: 30px;
    color: var(--blue-brand);
  }
  .holder {
    position: absolute;
    right: 36px; top: 102px;
    text-align: right;
  }
  .holder-name { font-size: 22px; font-weight: 700; color: var(--blue-brand); }
  .holder-role { font-size: 14px; margin-top: 2px; }
  .rule {
    position: absolute;
    height: 1px;
    background: var(--rule);
  }
  .rule-top { right: 36px; top: 160px; width: 250px; }
  .rule-bottom { left: 38px; top: 196px; width: 250px; }
  .address {
    position: absolute;
    right: 36px; top: 172px;
    text-align: right;
    font-size: 13.5px;
    font-style: normal;
    line-height: 1.35;
  }
  .contacts {
    position: absolute;
    left: 44px; top: 206px;
    list-style: none;
    font-size: 14px;
    line-height: 1.4;
  }
  .contacts li { display: flex; align-items: center; gap: 10px; }
  .contacts svg { width: 12px; height: 12px; fill: var(--blue-brand); flex: none; }
</style>
</head>
<body>

  <section class="card card-front" aria-label="Business card front">
    <p class="brand-name">Velran Global Components</p>
    <p class="front-web">www.velrancomponents-example<span class="tld">.co.uk</span></p>
  </section>

  <section class="card card-back" aria-label="Business card back">
    <p class="brand-name">Velran Global Components</p>

    <div class="holder">
      <p class="holder-name">Marcus Tellow</p>
      <p class="holder-role">Manager</p>
    </div>
    <div class="rule rule-top"></div>

    <address class="address">
      17 Marlow Yard, Upper Heath<br>
      Warwick, CV31 8QL<br>
      United Kingdom
    </address>

    <div class="rule rule-bottom"></div>
    <ul class="contacts">
      <li>
        <svg viewBox="0 0 12 12" aria-hidden="true"><path d="M2.4 0.6 L4.4 2.8 L3.4 4.2 C4.2 5.8 5.6 7.4 7.6 8.6 L9 7.6 L11.4 9.6 L10.2 11.4 C5.2 11 1 6.8 0.6 1.8 Z"/></svg>
        512 004 3920
      </li>
      <li>
        <svg viewBox="0 0 12 12" aria-hidden="true"><path d="M3 0.5 H9 V11.5 H3 Z M4 1.8 V8.8 H8 V1.8 Z M5.5 9.6 H6.5 V10.6 H5.5 Z"/></svg>
        512 004 3921
      </li>
      <li>
        <svg viewBox="0 0 12 12" aria-hidden="true"><path d="M0.5 2.5 H11.5 V9.5 H0.5 Z M1.5 3.4 L6 6.6 L10.5 3.4 V3.2 H1.5 Z"/></svg>
        info@velrancomponents-example.co.uk
      </li>
      <li>
        <svg viewBox="0 0 12 12" aria-hidden="true"><circle cx="6" cy="6" r="5.5"/><path d="M0.5 6 H11.5 M6 0.5 C3.5 3 3.5 9 6 11.5 M6 0.5 C8.5 3 8.5 9 6 11.5" stroke="#fff" stroke-width="0.8" fill="none"/></svg>
        www.velrancomponents-example.co.uk
      </li>
    </ul>
  </section>

</body>
</html>
```